Home Page Design for Motor Manufacturer

Hello,
please design the homepage for a manufacturer of industry motors. I am looking for a professional, clean and minimalistic design. Since this a rather conservative industry it should get a professional look but since it is a redesign there should be some modern that gives is the modern touch of innovation.
A competitor's homepage I like is:
https://www.valdorix.example/en/
What I like about this website:
* clean, minimal, well structured design
* mega menu
For this project please find attached the wireframes (most buttons are in German but by context and Google translate you will easily figure it out; only unclear - "Messe" means "trade exhibition"). The paddings and margins are NOT exact. Also any color of backgrounds etc. chosen is not meant to represent a real color but rather to illustrate the object and maybe show there should be some background emphasis (color or image).
Wireframes:
https: //www.filnest. example / t / pQmW7zKtRb3LyaHx
In both wireframes the only thing that is different is the Service section. I expect from the winner both designs for this service section: one with normal cart design and one with tabs as filters to search products (find image for product categories attached)
In the header use on the left the following text:
h1: "Your competent partner for industrial engines,
-transmission and drawing parts
with more than 5000 satisfied customers "
primary button: Our products
sec. button: Download catalog
and on the right side we feature one or more product images (like putting them in a nice display together).
I also think of a solid background color or subtle gradient for the hero section.
The winner should also design an open mega menu version.
Menu items in this order:
• Home page
• Gearboxes & Motors
• Engine components
• Drawing parts
• Machines & accessories
• About us
• Contact
Also create a language switch with globe symbol and DE for Germany and EN for English above the nav plus the telephone number with icon (user dummy number +49 (0) 987654321)
Output should be in Figma, Sketch or PSD.
Fonts + color to use:
header: Proza Libre, bold, # 0171A1
body: Open Sans, regular, black
Primary accent color: # 0171A1
Text black or dark gray
background: light gray, white or shade of blue
More image resources:
https://www.filnest.example/t/ZuTn4VcqMh8ErwJo
If there are any questions please do not hesitate to ask.
Target Market(s)
B2B - anyone with industrial machinery needing small motors (not car engines)
Industry/Entity Type
Manufacturing
Number of Pages Required
1 page
Requirements
Must have
- see above
Nice to have
- see above
Should not have
- see above

```html
<!DOCTYPE html>
<html lang="en">
<head>
<meta charset="utf-8">
<title>TORVEX – Industrial Engines, Transmission and Drawing Parts</title>
<link rel="stylesheet" href="https://fonts.googleapis.com/css2?family=Open+Sans:wght@400;600;700&family=Proza+Libre:wght@500;600;700&display=swap">
<style>
:root{
  --blue:#0171a1;
  --blue-mid:#0a76a8;
  --blue-deep:#0a4b77;
  --blue-hero-a:#0a78ab;
  --blue-hero-b:#085b8c;
  --ink:#222;
  --text:#444;
  --gray-bg:#f3f2f2;
  --card-bg:#f4f4f4;
  --line:#e2e2e2;
  --footer:#2a2a2a;
  --footer-bar:#3a3a3a;
  --white:#fff;
}
*{box-sizing:border-box;margin:0;padding:0}
html,body{width:1200px;height:4461px;overflow:hidden}
body{position:relative;background:var(--white);font-family:"Open Sans",sans-serif;color:var(--ink)}
.abs{position:absolute}
h1,h2,h3,.heading{font-family:"Proza Libre",sans-serif}

/* top bar */
.topbar{left:0;top:0;width:1200px;height:73px;background:#f1f1f1}
.brand{left:121px;top:16px;font-family:"Proza Libre",sans-serif;font-weight:700;font-size:34px;letter-spacing:1px;color:var(--blue-deep);line-height:40px}
.lang{left:818px;top:24px;width:72px;height:28px;background:#fff;border-radius:3px;display:flex;align-items:center;gap:10px;padding-left:6px}
.flag{width:30px;height:18px;background:linear-gradient(135deg,#1e3f8f 0 40%,#d83040 40% 60%,#1e3f8f 60%);border:1px solid #ddd}
.phone-top{left:912px;top:26px;display:flex;align-items:center;gap:10px;font-size:14px;color:#555}
.navbar{left:0;top:73px;width:1200px;height:55px;background:#fff;border-bottom:1px solid #e3e3e3}
.nav-item{top:92px;font-size:15px;color:#333;white-space:nowrap}
.nav-item.active{color:var(--blue)}
.caret{font-size:10px;color:#888;margin-left:5px}

/* hero */
.hero{left:0;top:128px;width:1200px;height:622px;background:linear-gradient(180deg,var(--blue-hero-a),var(--blue-hero-b))}
.hero-title{left:121px;top:298px;width:520px;color:#fff;font-weight:700;font-size:36px;line-height:52px}
.hero-sub{left:121px;top:424px;color:#fff;font-size:20px;line-height:35px}
.btn-pill{left:121px;top:523px;width:153px;height:38px;border-radius:19px;background:#1a9bd0;color:#fff;font-size:16px;line-height:38px;text-align:center}
.hero-ring{left:640px;top:228px;width:372px;height:372px;border-radius:50%;border:9px solid #1b9ccf;background:#fff;padding:10px}
.hero-photo{width:100%;height:100%;border-radius:50%;background:radial-gradient(circle at 50% 50%,#9fb3c4 0,#e9eef2 60%,#fff 75%)}
.thumb{left:1028px;width:60px;height:60px;border-radius:50%;background:radial-gradient(circle,#9aa7b3,#dfe6ec);border:3px solid rgba(255,255,255,.6)}
.thumb.sel{left:1022px;width:74px;height:74px;border:4px solid #fff}

/* why */
.sec-title{width:1200px;left:0;text-align:center;font-weight:500;font-size:44px;color:#2b2b2b}
.why-intro{left:250px;top:880px;width:700px;text-align:center;font-size:15px;line-height:27px;color:#333}
.why-card{width:461px;height:232px;color:#fff}
.why-card.dark{background:var(--blue-deep)}
.why-card.light{background:var(--blue-mid)}
.why-card svg{position:absolute;left:44px;top:50px}
.why-card h3{position:absolute;left:159px;top:44px;font-size:22px;font-weight:600}
.why-card p{position:absolute;left:159px;top:86px;width:255px;font-size:13.5px;line-height:24px}

/* products */
.products{left:0;top:1616px;width:1200px;height:977px;background:var(--gray-bg)}
.prod-card{width:270px;height:308px;background:#fff;border:1px solid #e4e4e4;box-shadow:0 2px 6px rgba(0,0,0,.05)}
.prod-card.sel{border:2px solid var(--blue)}
.prod-img{position:absolute;left:40px;top:24px;width:190px;height:170px;border-radius:8px;background:radial-gradient(ellipse at 50% 45%,#8f9aa5 0,#c9d0d6 45%,#fff 72%)}
.prod-name{position:absolute;left:0;top:220px;width:100%;text-align:center;font-size:20px;color:#222}
.prod-btn{position:absolute;left:75px;top:280px;width:120px;height:38px;background:#222;color:#fff;font-size:16px;line-height:38px;text-align:center;border-radius:2px}
.prod-card.sel .prod-btn{background:var(--blue)}

/* trade */
.trade-card{width:459px;height:198px;background:var(--card-bg);border-bottom:3px solid var(--blue)}
.trade-img{position:absolute;left:0;top:0;width:190px;height:195px;background:linear-gradient(160deg,#4a6a8f,#b9c3cf 55%,#e8e2d6)}
.trade-card h3{position:absolute;left:222px;top:30px;font-family:"Open Sans",sans-serif;font-weight:400;font-size:17px;color:#222}
.trade-card p{position:absolute;left:222px;top:62px;width:215px;font-size:13px;line-height:24px;color:#444}
.t-btn{position:absolute;top:145px;height:26px;font-size:12.5px;line-height:26px;color:#fff;text-align:center}
.t-btn.tickets{left:222px;width:98px;background:var(--blue)}
.t-btn.details{left:328px;width:82px;background:var(--blue-deep)}

/* about */
.about{left:0;top:3273px;width:1200px;height:650px;background:linear-gradient(120deg,#fff 0,#fff 60%,#e8f4f8 80%,#f7fbfc)}
.about-img{left:113px;top:3388px;width:587px;height:412px;background:linear-gradient(90deg,#fff 0,#f2f2f2 20%,#c7cbcd 45%,#e6b640 80%,#d39a10)}
.about-box{left:558px;top:3438px;width:530px;height:312px;background:#fff;border:2px solid var(--blue-deep);border-radius:4px}
.about-box h2{position:absolute;left:55px;top:34px;font-size:34px;font-weight:500;color:#2b2b2b}
.about-box p{position:absolute;left:55px;width:430px;font-size:14px;line-height:25px;color:#333}

/* ebook */
.ebook{left:0;top:3923px;width:1200px;height:196px;background:linear-gradient(90deg,#0a5f91,#0a76a8)}
.ebook-title{left:462px;top:3944px;color:#fff;font-weight:500;font-size:34px}
.ebook-sub{left:462px;top:3998px;color:#fff;font-size:17px}
.ebook-btn{left:462px;top:4047px;width:168px;height:40px;border-radius:20px;background:#1d1d1d;color:#fff;font-size:15px;font-weight:600;line-height:40px;text-align:center}

/* footer */
.footer{left:0;top:4119px;width:1200px;height:277px;background:var(--footer)}
.footer-bar{left:0;top:4396px;width:1200px;height:65px;background:var(--footer-bar);color:#ddd;font-size:14px}
.f-brand{left:121px;top:4186px;color:#fff;font-family:"Proza Libre",sans-serif;font-weight:700;font-size:54px;letter-spacing:2px}
.social{top:4314px;width:20px;height:20px;border:2px solid #fff;border-radius:50%}
.f-head{top:4184px;color:#fff;font-size:15px;font-weight:600}
.f-text{color:#ddd;font-size:13.5px;line-height:24px}
.f-row{display:flex;gap:14px;align-items:flex-start}
.f-call{left:862px;top:4300px;width:178px;height:40px;background:var(--blue);border-radius:20px;color:#fff;font-size:15px;line-height:40px;padding-left:60px}
.f-call-icon{position:absolute;left:2px;top:2px;width:36px;height:36px;border-radius:50%;background:#111;border:2px solid #fff}
</style>
</head>
<body>

<!-- top bar -->
<div class="abs topbar"></div>
<div class="abs brand">TORVEX</div>
<div class="abs lang"><span class="flag"></span><svg width="10" height="6"><path d="M0 0h10L5 6z" fill="#666"/></svg></div>
<div class="abs phone-top">
  <svg width="20" height="20" viewBox="0 0 24 24"><circle cx="12" cy="12" r="11" fill="#fff" stroke="#bbb"/><path d="M8 6l2 3-1.3 1.5c.8 1.6 2.2 3 3.8 3.8L14 13l3 2-1 2.5c-4.5-.3-8.2-4-8.5-8.5z" fill="#777"/></svg>
  <span>+49 (0) 987654321</span>
</div>

<div class="abs navbar"></div>
<div class="abs nav-item active" style="left:118px">Home</div>
<div class="abs nav-item" style="left:192px">Gearboxes &amp; Motors<span class="caret">▾</span></div>
<div class="abs nav-item" style="left:384px">Engine Components<span class="caret">▾</span></div>
<div class="abs nav-item" style="left:573px">Drawing parts<span class="caret">▾</span></div>
<div class="abs nav-item" style="left:719px">Machines &amp; Accessories<span class="caret">▾</span></div>
<div class="abs nav-item" style="left:932px">About Us</div>
<div class="abs nav-item" style="left:1027px">Contact</div>

<!-- hero -->
<section class="abs hero"></section>
<svg class="abs" style="left:0;top:640px" width="1200" height="112" viewBox="0 0 1200 112"><path d="M0 112V108C300 45 800 20 1200 60V112z" fill="#fff"/></svg>
<h1 class="abs hero-title">Your Competent Partner For Industrial Engines</h1>
<div class="abs hero-sub">Transmission And Drawing Parts<br>With More Than 5000 Satisfied Customers</div>
<div class="abs btn-pill">Learn More</div>
<div class="abs hero-ring"><div class="hero-photo" role="img" aria-label="Planetary gear motor product photo"></div></div>
<svg class="abs" style="left:1047px;top:272px" width="22" height="12"><path d="M1 11L11 1l10 10" fill="none" stroke="#8cc3de" stroke-width="2"/></svg>
<div class="abs thumb" style="top:311px" role="img" aria-label="Angle gear motor thumbnail"></div>
<div class="abs thumb sel" style="top:384px" role="img" aria-label="Planetary gear motor thumbnail"></div>
<div class="abs thumb" style="top:470px" role="img" aria-label="Motor thumbnail"></div>
<svg class="abs" style="left:1047px;top:528px" width="22" height="12"><path d="M1 1l10 10L21 1" fill="none" stroke="#8cc3de" stroke-width="2"/></svg>

<!-- why choose us -->
<h2 class="abs sec-title" style="top:804px">Why Choose Us</h2>
<p class="abs why-intro">Lorem Ipsum is simply dummy text of the printing and typesetting industry. Lorem Ipsum has been the industry's standard dummy text ever since the 1500s Lorem Ipsum is simply dummy text of the printing and typesetting industry.</p>

<div class="abs why-card dark" style="left:130px;top:1004px">
  <svg width="76" height="76" viewBox="0 0 76 76" fill="none" stroke="#fff" stroke-width="4"><circle cx="38" cy="20" r="11"/><path d="M18 46c2-10 10-15 20-15s18 5 20 15"/><path d="M14 50l3 6 6 1-5 4 1 6-5-3-5 3 1-6-5-4 6-1z M38 50l3 6 6 1-5 4 1 6-5-3-5 3 1-6-5-4 6-1z M62 50l3 6 6 1-5 4 1 6-5-3-5 3 1-6-5-4 6-1z" fill="#fff" stroke-width="1"/></svg>
  <h3>Customer Satisfaction</h3>
  <p>Lorem Ipsum is simply dummy text of the printing and typesetting industry. Lorem Ipsum has been the industry's standard dummy text ever.</p>
</div>
<div class="abs why-card light" style="left:610px;top:1004px">
  <svg width="76" height="76" viewBox="0 0 76 76" fill="none" stroke="#fff" stroke-width="4"><path d="M38 4l8 6 10-1 4 9 9 4-1 10 6 8-6 8 1 10-9 4-4 9-10-1-8 6-8-6-10 1-4-9-9-4 1-10-6-8 6-8-1-10 9-4 4-9 10 1z" stroke-width="3"/><circle cx="38" cy="40" r="20"/><path d="M45 32c-2-3-11-4-12 1s13 4 12 10-11 5-13 1M38 26v28" stroke-width="3.5"/></svg>
  <h3>Optimal Price</h3>
  <p>Lorem Ipsum is simply dummy text of the printing and typesetting industry. Lorem Ipsum has been the industry's standard dummy text ever.</p>
</div>
<div class="abs why-card light" style="left:130px;top:1256px">
  <svg width="76" height="76" viewBox="0 0 76 76" fill="none" stroke="#fff" stroke-width="5"><circle cx="26" cy="38" r="10"/><path d="M26 18v6M26 52v6M6 38h6M40 38h6M12 24l4 4M36 48l4 4M12 52l4-4M36 28l4-4" stroke-linecap="round"/><circle cx="56" cy="18" r="6" stroke-width="4"/><circle cx="56" cy="58" r="6" stroke-width="4"/><path d="M56 6v4M56 26v4M44 18h4M64 18h4M56 46v4M56 66v4M44 58h4M64 58h4" stroke-width="4" stroke-linecap="round"/></svg>
  <h3>Smooth Implementation</h3>
  <p>Lorem Ipsum is simply dummy text of the printing and typesetting industry. Lorem Ipsum has been the industry's standard dummy text ever.</p>
</div>
<div class="abs why-card dark" style="left:610px;top:1256px">
  <svg width="76" height="76" viewBox="0 0 76 76" fill="none" stroke="#fff" stroke-width="4"><circle cx="38" cy="28" r="22"/><path d="M38 16l4 8 8 1-6 6 2 8-8-4-8 4 2-8-6-6 8-1z" stroke-width="3"/><path d="M22 46L12 66l10-2 5 8 9-20M54 46l10 20-10-2-5 8-9-20" fill="#fff"/></svg>
  <h3>High Quality Performance</h3>
  <p>Lorem Ipsum is simply dummy text of the printing and typesetting industry. Lorem Ipsum has been the industry's standard dummy text ever.</p>
</div>

<!-- products -->
<section class="abs products"></section>
<h2 class="abs sec-title" style="top:1696px">Our Products</h2>

<div class="abs prod-card" style="left:163px;top:1798px"><div class="prod-img" role="img" aria-label="Right-angle gearbox"></div><div class="prod-name">Product Category</div><div class="prod-btn">Details</div></div>
<div class="abs prod-card sel" style="left:464px;top:1798px"><div class="prod-img" role="img" aria-label="Planetary gear motor"></div><div class="prod-name">Product Category</div><div class="prod-btn">Details</div></div>
<div class="abs prod-card" style="left:767px;top:1798px"><div class="prod-img" role="img" aria-label="DC gear motor"></div><div class="prod-name">Product Category</div><div class="prod-btn">Details</div></div>
<div class="abs prod-card" style="left:163px;top:2149px"><div class="prod-img" role="img" aria-label="Precision reducer bearing"></div><div class="prod-name">Product Category</div><div class="prod-btn">Details</div></div>
<div class="abs prod-card" style="left:464px;top:2149px"><div class="prod-img" role="img" aria-label="Compact planetary motor"></div><div class="prod-name">Product Category</div><div class="prod-btn">Details</div></div>
<div class="abs prod-card" style="left:767px;top:2149px"><div class="prod-img" role="img" aria-label="Right-angle gearbox"></div><div class="prod-name">Product Category</div><div class="prod-btn">Details</div></div>

<!-- trade exhibition -->
<h2 class="abs sec-title" style="top:2664px">Trade Exhibition</h2>

<div class="abs trade-card" style="left:133px;top:2752px"><div class="trade-img" role="img" aria-label="Trade fair hall with exhibition stands"></div><h3>Trade Exhibition</h3><p>Lorem Ipsum is simply dummy text of the printing and typesetting industry.</p><div class="t-btn tickets">Free tickets</div><div class="t-btn details">Details</div></div>
<div class="abs trade-card" style="left:610px;top:2752px"><div class="trade-img" role="img" aria-label="Visitors in a blue-lit exhibition hall" style="background:linear-gradient(160deg,#1d3f8a,#6d8cc4 55%,#cfd7e6)"></div><h3>Trade Exhibition</h3><p>Lorem Ipsum is simply dummy text of the printing and typesetting industry.</p><div class="t-btn tickets">Free tickets</div><div class="t-btn details">Details</div></div>
<div class="abs trade-card" style="left:133px;top:2972px"><div class="trade-img" role="img" aria-label="Bright exhibition booth area" style="background:linear-gradient(160deg,#5b5a44,#c8c6b2 50%,#eceae0)"></div><h3>Trade Exhibition</h3><p>Lorem Ipsum is simply dummy text of the printing and typesetting industry.</p><div class="t-btn tickets">Free tickets</div><div class="t-btn details">Details</div></div>
<div class="abs trade-card" style="left:610px;top:2972px"><div class="trade-img" role="img" aria-label="Visitors walking through a fair hall" style="background:linear-gradient(160deg,#3b3f48,#a9adb5 50%,#e4e6ea)"></div><h3>Trade Exhibition</h3><p>Lorem Ipsum is simply dummy text of the printing and typesetting industry.</p><div class="t-btn tickets">Free tickets</div><div class="t-btn details">Details</div></div>

<!-- about -->
<section class="abs about"></section>
<div class="abs about-img" role="img" aria-label="Lubrication pump unit in front of golden oil splash"></div>
<div class="abs about-box">
  <h2>About Us</h2>
  <p style="top:104px">Lorem Ipsum is simply dummy text of the printing and typesetting industry. Lorem Ipsum has been the industry's standard dummy text ever since the 1500s</p>
  <p style="top:198px">Lorem Ipsum is simply dummy text of the printing and typesetting industry. Lorem Ipsum has been the industry's standard dummy text ever since the 1500s</p>
</div>

<!-- ebook -->
<section class="abs ebook"></section>
<svg class="abs" style="left:150px;top:3923px" width="240" height="196" viewBox="0 0 240 196">
  <path d="M30 0H215L240 98 215 196H30Z" fill="#fff" opacity=".9"/>
  <path d="M48 12H178L210 98 178 184H48L14 98Z" fill="#0a4b77" stroke="#0a4b77" stroke-width="8" stroke-linejoin="round"/>
  <rect x="96" y="42" width="26" height="40" rx="4" fill="none" stroke="#fff" stroke-width="2.5"/>
  <rect x="110" y="54" width="22" height="16" rx="2" fill="#0a4b77" stroke="#fff" stroke-width="2.5"/>
  <text x="112" y="128" fill="#fff" font-family="Open Sans, sans-serif" font-size="23" text-anchor="middle">Ebook</text>
</svg>
<h2 class="abs ebook-title">Lorem Ipsum is simply dummy text</h2>
<div class="abs ebook-sub">Lorem Ipsum has been the industry's standard dummy</div>
<div class="abs ebook-btn">Download Now</div>

<!-- footer -->
<footer class="abs footer"></footer>
<div class="abs f-brand">TORVEX</div>
<div class="abs social" style="left:174px"></div>
<div class="abs social" style="left:212px"></div>
<div class="abs social" style="left:256px"></div>

<div class="abs f-head" style="left:414px">Contact Us</div>
<div class="abs f-text" style="left:412px;top:4222px">
  <div class="f-row"><svg width="14" height="18" viewBox="0 0 14 18"><path d="M7 1a6 6 0 016 6c0 4-6 10-6 10S1 11 1 7a6 6 0 016-6z" fill="none" stroke="#ddd" stroke-width="1.5"/><circle cx="7" cy="7" r="2" fill="#ddd"/></svg><span style="margin-left:2px">48 Harlow Avenue<br>Address 20417 TX</span></div>
  <div class="f-row" style="margin-top:8px"><svg width="16" height="16" viewBox="0 0 24 24"><path d="M6 2l4 5-2 2c1.5 3 4 5.5 7 7l2-2 5 4-2 4C10 21 3 14 2 4z" fill="#ddd"/></svg><span>+49 (0) 987654321</span></div>
  <div class="f-row" style="margin-top:8px"><svg width="16" height="14" viewBox="0 0 16 14"><rect x="1" y="2" width="14" height="10" fill="#ddd"/><path d="M1 2l7 6 7-6" fill="none" stroke="#2a2a2a" stroke-width="1.5"/></svg><span>name@mailbox.example</span></div>
</div>

<div class="abs f-head" style="left:675px">Company</div>
<div class="abs f-text" style="left:675px;top:4215px">Home<br>Gearboxes &amp; Motors<br>Engine Components<br>Drawing Parts<br>Machines &amp; Accessories</div>

<div class="abs f-head" style="left:862px;top:4187px;font-weight:400">Stil have questions?</div>
<div class="abs f-text" style="left:862px;top:4224px;width:240px">A repesentative will aswer your questions as soon as possible.</div>
<div class="abs f-call"><span class="f-call-icon"><svg width="32" height="32" viewBox="0 0 24 24"><path d="M8 6l2 3-1.3 1.5c.8 1.6 2.2 3 3.8 3.8L14 13l3 2-1 2.5c-4.5-.3-8.2-4-8.5-8.5z" fill="#fff"/></svg></span>Contact Now</div>

<div class="abs footer-bar">
  <span style="position:absolute;left:142px;top:22px">Copyright 2020 Torvex. All Rights Reserved.</span>
  <span style="position:absolute;left:840px;top:22px;font-size:13px">Privacy Policy &nbsp;&nbsp;|&nbsp;&nbsp; Terms Of Services</span>
</div>

</body>
</html>
```